Business Card Design - Amberfield Court

We are looking at a new design for our business cards that has a modern and professional look. We run a residential aged care facility focussing on the care of residents. The cards will be used for potential clients, consultants and business opportunities in this sector. Blue and white is our main colours and would to see these colours incorporated in the design.
Industry/Entity Type
Business
Contact Information for Business Card
Amberfield Court, Darren Walsh, dwalsh@amberfieldcourt.com.au, Finance Manager, 0472 639 208, BCom, 37 Marrabel Crescent, Brindle Vale, Qld 4093.
Look and feel
Each slider illustrates characteristics of the customer's brand and the style your logo design should communicate.

```html
<!DOCTYPE html>
<html lang="en">
<head>
<meta charset="utf-8">
<title>Amberfield Court – Business Card</title>
<link href="https://fonts.googleapis.com/css2?family=Open+Sans:wght@400;600;700&display=swap" rel="stylesheet">
<style>
  :root {
    --brand-blue: #4a7893;
    --brand-black: #050505;
    --brand-taupe: #b2a69d;
    --paper-white: #ffffff;
    --backdrop: #e6e6e4;
    --card-w: 540px;
    --card-h: 320px;
  }
  * { box-sizing: border-box; margin: 0; padding: 0; }
  html, body {
    width: 1200px; height: 900px; overflow: hidden;
    background: var(--backdrop);
    font-family: "Open Sans", Arial, sans-serif;
  }
  .sheet {
    width: 1200px; height: 900px;
    display: flex; align-items: center; justify-content: center; gap: 40px;
  }
  .card {
    position: relative;
    width: var(--card-w); height: var(--card-h);
    overflow: hidden;
    box-shadow: 0 4px 14px rgba(0,0,0,0.18);
  }

  /* Logo side */
  .card--brand { background: var(--brand-blue); }
  .brand-lockup {
    position: absolute; inset: 0;
    display: flex; align-items: center; justify-content: center; gap: 14px;
  }
  .brand-mark {
    width: 30px; height: 30px; border-radius: 50%;
    background: var(--paper-white);
  }
  .brand-name {
    color: var(--paper-white);
    font-weight: 600; font-size: 30px; letter-spacing: 0.06em;
    text-transform: uppercase;
  }

  /* Contact side */
  .card--contact { background: var(--brand-blue); }
  .contact-backdrop { position: absolute; inset: 0; }
  .contact-lockup {
    position: absolute; left: 26px; top: 128px;
    display: flex; align-items: center; gap: 10px;
  }
  .contact-lockup .brand-mark { width: 20px; height: 20px; background: var(--brand-blue); }
  .contact-lockup .brand-name { color: var(--brand-blue); font-size: 19px; letter-spacing: 0.05em; }

  .contact-details {
    position: absolute; right: 30px; top: 40px;
    text-align: right; color: var(--paper-white);
  }
  .person-name { font-weight: 700; font-size: 20px; line-height: 1.2; }
  .person-name .credential { font-size: 14px; }
  .person-role { font-size: 15px; line-height: 1.3; margin-bottom: 26px; }
  .address { font-size: 15px; line-height: 1.45; margin-bottom: 26px; }
  .contact-line {
    display: flex; justify-content: flex-end; align-items: center; gap: 8px;
    font-size: 15px; line-height: 1.5;
  }
  .contact-line svg { width: 13px; height: 13px; fill: var(--paper-white); }
</style>
</head>
<body>
<main class="sheet">

  <section class="card card--contact">
    <svg class="contact-backdrop" viewBox="0 0 540 320" width="540" height="320" aria-hidden="true">
      <path d="M0,0 H268 Q335,165 222,320 H0 Z" fill="var(--brand-taupe)"/>
      <path d="M0,0 H246 Q312,160 200,320 H0 Z" fill="var(--brand-black)"/>
    </svg>
    <div class="contact-lockup">
      <span class="brand-mark"></span>
      <span class="brand-name">Amberfield Court</span>
    </div>
    <div class="contact-details">
      <p class="person-name">Darren Walsh, <span class="credential">BCom</span></p>
      <p class="person-role">Finance Manager</p>
      <p class="address">37 Marrabel Crescent<br>, Brindle Vale, Qld 4093</p>
      <p class="contact-line">0472 639 208
        <svg viewBox="0 0 24 24" aria-hidden="true"><path d="M6.6 10.8a15.1 15.1 0 0 0 6.6 6.6l2.2-2.2a1 1 0 0 1 1-.25 11.4 11.4 0 0 0 3.6.57 1 1 0 0 1 1 1V20a1 1 0 0 1-1 1A17 17 0 0 1 3 4a1 1 0 0 1 1-1h3.5a1 1 0 0 1 1 1c0 1.25.2 2.45.57 3.6a1 1 0 0 1-.25 1z"/></svg>
      </p>
      <p class="contact-line">dwalsh@amberfieldcourt.com.au
        <svg viewBox="0 0 24 24" aria-hidden="true"><path d="M2 5h20v14H2z M3.5 6.5 12 13l8.5-6.5" stroke="var(--brand-blue)" stroke-width="1.6"/></svg>
      </p>
    </div>
  </section>

  <section class="card card--brand">
    <div class="brand-lockup">
      <span class="brand-mark"></span>
      <span class="brand-name">Amberfield Court</span>
    </div>
  </section>

</main>
</body>
</html>
```